Redesign of business card for Cedar Ridge Mechanical

We are looking for a new design for our business cards for Cedar Ridge Mechanical. We are a plumbing & HVAC construction company, operating on the West Coast of Canada and USA. Logo attached.
Industry/Entity Type
Construction - Plumbing & HVAC
Contact Information for Business Card
Name, address, phone numbers, email, website address
Look and feel
Each slider illustrates characteristics of the customer's brand and the style your logo design should communicate.

```html
<!DOCTYPE html>
<html lang="en">
<head>
<meta charset="UTF-8">
<title>Cedar Ridge Mechanical – Business Card</title>
<link href="https://fonts.googleapis.com/css2?family=Poppins:wght@300;400;600&display=swap" rel="stylesheet">
<style>
  :root {
    --backdrop: #222222;
    --card: #1c1c1e;
    --ink: #ffffff;
    --ink-soft: #d9d9d9;
    --pattern-a: #1a1a1c;
    --pattern-b: #2a2a2d;
  }
  * { box-sizing: border-box; margin: 0; padding: 0; }
  html, body { width: 1200px; height: 780px; overflow: hidden; }
  body {
    background: var(--backdrop);
    font-family: "Poppins", sans-serif;
    color: var(--ink);
    display: flex;
    align-items: center;
    justify-content: center;
    gap: 40px;
  }
  .card {
    width: 500px;
    height: 286px;
    background: var(--card);
    border-radius: 4px;
    position: relative;
    overflow: hidden;
  }
  .card-front { padding: 24px 26px; }
  .holder { position: absolute; top: 22px; left: 26px; }
  .holder-name { font-size: 21px; line-height: 1.1; letter-spacing: 0.5px; }
  .holder-first { font-weight: 600; }
  .holder-last { font-weight: 300; }
  .holder-role { font-size: 10.5px; font-weight: 300; letter-spacing: 0.6px; margin-top: 2px; }

  .brand {
    position: absolute;
    top: 78px;
    right: 26px;
    display: flex;
    align-items: center;
    gap: 10px;
  }
  .brand-square {
    width: 30px; height: 30px;
    border: 3px solid var(--ink);
    border-radius: 6px;
  }
  .brand-name {
    font-size: 15px;
    font-weight: 600;
    letter-spacing: 1px;
    text-transform: uppercase;
  }

  .contact {
    position: absolute;
    right: 26px;
    bottom: 20px;
    text-align: right;
    font-size: 11.5px;
    font-weight: 300;
    line-height: 1.5;
    color: var(--ink-soft);
  }
  .address { margin-bottom: 6px; }
  .contact-line { display: flex; align-items: center; justify-content: flex-end; gap: 8px; }
  .contact-line svg { width: 12px; height: 12px; fill: var(--ink); flex: none; }

  .card-back .pattern {
    position: absolute; inset: 0;
    background: linear-gradient(135deg, var(--pattern-a) 0%, var(--pattern-b) 60%, var(--pattern-a) 100%);
  }
</style>
</head>
<body>
  <section class="card card-front">
    <div class="holder">
      <p class="holder-name"><span class="holder-first">Marta</span> <span class="holder-last">Lindqvist</span></p>
      <p class="holder-role">Founder &amp; CEO</p>
    </div>

    <div class="brand">
      <span class="brand-square"></span>
      <span class="brand-name">Cedar Ridge Mechanical</span>
    </div>

    <div class="contact">
      <p class="address">1840 Harbor Rd. Suite 310<br>Portland, OR 97209</p>
      <p class="contact-line">(503) 555-0147
        <svg viewBox="0 0 24 24" aria-hidden="true"><path d="M6.6 10.8a15.1 15.1 0 0 0 6.6 6.6l2.2-2.2a1 1 0 0 1 1-.25 11.4 11.4 0 0 0 3.6.57 1 1 0 0 1 1 1V20a1 1 0 0 1-1 1A17 17 0 0 1 3 4a1 1 0 0 1 1-1h3.5a1 1 0 0 1 1 1c0 1.25.2 2.45.57 3.57a1 1 0 0 1-.25 1z"/></svg>
      </p>
      <p class="contact-line">info@yourwebsite.com
        <svg viewBox="0 0 24 24" aria-hidden="true"><path d="M12 2a10 10 0 1 0 0 20 10 10 0 0 0 0-20zm6.9 6h-3a15.7 15.7 0 0 0-1.4-3.6A8 8 0 0 1 18.9 8zM12 4c.8 1.2 1.5 2.5 1.9 4h-3.8c.4-1.5 1.1-2.8 1.9-4zM4.3 14a8.2 8.2 0 0 1 0-4h3.4a16.5 16.5 0 0 0 0 4zm.8 2h3a15.7 15.7 0 0 0 1.4 3.6A8 8 0 0 1 5.1 16zm3-8h-3a8 8 0 0 1 4.4-3.6A15.7 15.7 0 0 0 8.1 8zM12 20c-.8-1.2-1.5-2.5-1.9-4h3.8c-.4 1.5-1.1 2.8-1.9 4zm2.3-6H9.7a14.7 14.7 0 0 1 0-4h4.6a14.7 14.7 0 0 1 0 4zm.2 5.6a15.7 15.7 0 0 0 1.4-3.6h3a8 8 0 0 1-4.4 3.6zm1.8-5.6a16.5 16.5 0 0 0 0-4h3.4a8.2 8.2 0 0 1 0 4z"/></svg>
      </p>
      <p class="contact-line">www.yourwebsite.com
        <svg viewBox="0 0 24 24" aria-hidden="true"><path d="M3 5h18a1 1 0 0 1 1 1v12a1 1 0 0 1-1 1H3a1 1 0 0 1-1-1V6a1 1 0 0 1 1-1zm9 7.2L4.5 7.3v1.9L12 14l7.5-4.8V7.3z"/></svg>
      </p>
    </div>
  </section>

  <section class="card card-back">
    <div class="pattern" role="img" aria-label="Repeating brand pattern in tone-on-tone black with subtle gloss"></div>
  </section>
</body>
</html>
```